Dorwin's Coating & Renewal Letterhead Design We want to revamp out old traditional letterhead with the new logo designs that are attached. We are working on getting all our company items from vehicles, business, cards, t-shirts, letterhead to match. This should include company colors, fonts, and flow of items that we have attached below.

Industry/Entity Type

Construction Company

Font styles to use
Sans Serif
Other font styles liked:
• Bold with outline

Colors
ec1f27
ffffff

Requirements
Must have
• Company Name: Dorwin's Coating & Renewal
• Address: 4728 SW 81st Ter Halverd cove fl 39417
• Office Number: (555) 413-2986
• Email: Dorwinrenewal@mailbrook.example
• License Number: KRT8046392
Nice to have
• Company Colors: red, white, black, and grey

```html
<!DOCTYPE html>
<html lang="en">
<head>
<meta charset="utf-8">
<title>Dorwin's Coating &amp; Renewal — Letterhead</title>
<link rel="stylesheet" href="https://fonts.googleapis.com/css2?family=Montserrat:wght@400;600;700;800&display=swap">
<style>
  :root {
    --brand-red: #ec1f27;
    --ink: #333333;
    --swoosh-grey: #e8e8e8;
    --swoosh-blush: #f9d9d2;
    --paper: #ffffff;
    --backdrop: #b3b3b3;
  }
  * { margin: 0; padding: 0; box-sizing: border-box; }
  html, body { width: 995px; height: 1200px; overflow: hidden; }
  body {
    background: var(--backdrop);
    font-family: "Montserrat", sans-serif;
    color: var(--ink);
  }
  .letterhead {
    position: absolute;
    left: 73px; top: 0;
    width: 848px; height: 1200px;
    background: var(--paper);
    overflow: hidden;
  }
  .swooshes { position: absolute; inset: 0; width: 100%; height: 100%; }
  .brand-name {
    position: absolute; left: 60px; top: 52px;
    color: var(--brand-red); font-weight: 800; line-height: 1;
  }
  .brand-name .primary { display: block; font-size: 46px; letter-spacing: 1px; }
  .brand-name .secondary { display: block; font-size: 20px; margin-top: 8px; letter-spacing: 0.5px; }
  .address {
    position: absolute; right: 64px; top: 99px;
    text-align: right; font-style: normal; font-weight: 700; font-size: 16.5px; line-height: 20px;
  }
  .sign-off { position: absolute; left: 60px; top: 239px; font-size: 13.5px; line-height: 18px; }
  .signatory { position: absolute; left: 60px; top: 275px; }
  .signatory .name { font-size: 23px; font-weight: 700; letter-spacing: 0.5px; line-height: 26px; }
  .signatory .role { font-size: 16.5px; font-weight: 700; line-height: 20px; margin-top: 0; }
  .letter-body {
    position: absolute; left: 60px; top: 457px;
    font-size: 13.6px; line-height: 28px; white-space: nowrap;
  }
  .letter-body p + p { margin-top: 28px; }
  .letter-body p.gap { margin-top: 56px; }
  .rule {
    position: absolute; left: 231px; right: 0; top: 1085px;
    height: 2px; background: var(--brand-red);
  }
  .contact-list {
    position: absolute; left: 60px; top: 1077px;
    list-style: none; font-weight: 700; font-size: 16px;
  }
  .contact-list li { display: flex; align-items: center; height: 21px; line-height: 21px; }
  .contact-list svg { width: 18px; height: 18px; margin-right: 6px; flex: none; }
  .license {
    position: absolute; right: 64px; top: 1120px;
    font-weight: 700; font-size: 16.5px; line-height: 21px;
  }
  .license .code { color: var(--brand-red); }
</style>
</head>
<body>
  <main class="letterhead">
    <svg class="swooshes" viewBox="0 0 1182 1672" preserveAspectRatio="none" aria-hidden="true">
      <path fill="var(--swoosh-grey)" d="M0,376 Q700,320 1020,0 L1130,0 Q780,350 0,392 Z"/>
      <path fill="var(--swoosh-grey)" d="M705,296 Q1010,220 1182,40 L1182,110 Q1010,245 705,296 Z"/>
      <path fill="var(--swoosh-blush)" d="M270,1672 Q450,1570 695,1536 Q480,1600 370,1672 Z"/>
      <path fill="var(--swoosh-blush)" d="M690,1672 Q900,1570 1182,1532 Q960,1600 800,1672 Z"/>
    </svg>

    <div class="brand-name">
      <span class="primary">DORWIN'S</span>
      <span class="secondary">COATING &amp; RENEWAL</span>
    </div>

    <address class="address">4728 SW 81st Ter Halverd<br>cove fl 39417</address>

    <p class="sign-off">Sincearly,</p>
    <div class="signatory">
      <div class="name">JANE CARTER</div>
      <div class="role">Director</div>
    </div>

    <div class="letter-body">
      <p>This is a sample letter that has been placed to demonstrate typing remat (Your Company).letterhead<br>design. When positioned properly, it will serve to work in harmony with all other elements letterhead.<br>This letterhead design is meant to project an image &nbsp;This letterhead design is meant project an image<br>of professionalism reliability. By using simple aligen we have created a very spacious feeling.<br>The simplicity suggest &nbsp;rengththe spaciousnes contributes haesthetics the layout. These basic<br>qualities along with the (Your Company)</p>
      <p>look and helps reinforce the (Your Company) brand. letterhead design is meant to project an image<br>design. When positioned properly, it will serve to work in harmony all the other elements letterhead.<br>sionalism and reliability.</p>
      <p class="gap">This letterhead design is based on the (Form of your logo) form (Your Company) logo. Each stationery<br>we have created a very spacious feeling. The simplicity suggests strength the spaciousnes contribute<br>part of the (Form of your logo). This letterhead design is based on the (Form of your logo) form (Your<br>Company) logo. Each stationery we have created a very spacious feeling. The simplicity suggests<br>strength the spaciousnes contribute part of the (Form of your logo).</p>
    </div>

    <div class="rule"></div>
    <ul class="contact-list">
      <li>
        <svg viewBox="0 0 18 18" aria-hidden="true"><circle cx="9" cy="9" r="8" fill="none" stroke="var(--brand-red)" stroke-width="1.3"/><path d="M6.2 5 L7.6 4.8 L8.3 6.8 L7.4 7.6 Q8.2 9.6 10.2 10.6 L11 9.7 L13 10.4 L12.8 11.8 Q9.5 12.4 7.2 10.2 Q5.4 8 6.2 5 Z" fill="var(--brand-red)"/></svg>
        (555) 413-2986
      </li>
      <li>
        <svg viewBox="0 0 18 18" aria-hidden="true"><circle cx="9" cy="9" r="8" fill="none" stroke="var(--brand-red)" stroke-width="1.3"/><rect x="5.2" y="6.3" width="7.6" height="5.4" fill="var(--brand-red)"/><path d="M5.2 6.3 L9 9.2 L12.8 6.3" fill="none" stroke="#fff" stroke-width="0.8"/></svg>
        Dorwinrenewal@mailbrook.example
      </li>
      <li>
        <svg viewBox="0 0 18 18" aria-hidden="true"><circle cx="9" cy="9" r="8" fill="none" stroke="var(--brand-red)" stroke-width="1.3"/><circle cx="9" cy="9" r="4.2" fill="none" stroke="var(--brand-red)" stroke-width="0.8"/><ellipse cx="9" cy="9" rx="1.8" ry="4.2" fill="none" stroke="var(--brand-red)" stroke-width="0.8"/><path d="M4.8 9 H13.2" stroke="var(--brand-red)" stroke-width="0.8"/></svg>
        www.dorwinrenewal
      </li>
    </ul>
    <p class="license">License Number: <span class="code">KRT8046392</span></p>
  </main>
</body>
</html>
```